Business Card Design

We are a commercial real estate brokerage in San Francisco, leasing office buildings downtown.
I would like a clean, elegant look. Simple but powerful .

Industry/Entity Type

Business

Contact Information for Business Card

Derek Holloway
lic# 07258143
415.555.0172
derek@velt-commercial.example
velt-commercial.example

```html
<!DOCTYPE html>
<html lang="en">
<head>
<meta charset="utf-8">
<title>Velt Commercial – Business Cards</title>
<link rel="stylesheet" href="https://fonts.googleapis.com/css2?family=Open+Sans:wght@400;600;700&display=swap">
<style>
  :root {
    --page: #d9d9d7;
    --card-black: #000000;
    --band-black: #121212;
    --steel-blue: #8a9bbb;
    --slate-grey: #5f5f61;
    --text-white: #ffffff;
    --skyline-dark: #161616;
    --skyline-mid: #3c3c3e;
  }
  * { box-sizing: border-box; margin: 0; padding: 0; }
  html, body { width: 1200px; height: 900px; overflow: hidden; }
  body {
    background: var(--page);
    font-family: "Open Sans", Arial, sans-serif;
    display: flex;
    flex-direction: column;
    align-items: center;
    justify-content: center;
    gap: 44px;
  }
  .card {
    position: relative;
    width: 660px;
    height: 378px;
    background: var(--card-black);
    overflow: hidden;
    box-shadow: 0 6px 18px rgba(0,0,0,0.25);
  }
  .card__stripe-grey {
    position: absolute; left: 0; right: 0; bottom: 40px; height: 14px;
    background: var(--slate-grey);
  }
  .card__stripe-blue {
    position: absolute; left: 0; right: 0; bottom: 12px; height: 28px;
    background: var(--steel-blue);
  }
  .card__stripe-base {
    position: absolute; left: 0; right: 0; bottom: 0; height: 12px;
    background: var(--slate-grey);
  }
  .wordmark {
    color: var(--steel-blue);
    font-weight: 700;
    line-height: 0.9;
    text-transform: uppercase;
  }
  .wordmark__name { display: block; letter-spacing: 1px; }
  .wordmark__sub { display: block; letter-spacing: 1.5px; }

  /* Back card */
  .card--back .wordmark {
    position: absolute; left: 40px; top: 122px;
  }
  .card--back .wordmark__name { font-size: 72px; }
  .card--back .wordmark__sub { font-size: 30px; margin-top: 4px; }
  .card--back .skyline-decor {
    position: absolute; right: 30px; top: 30px;
    width: 300px; height: 294px;
    background: linear-gradient(180deg, var(--skyline-dark), #1d1d1d);
  }

  /* Front card */
  .card--front .contact-band {
    position: absolute; left: 0; right: 0; top: 176px; height: 148px;
    background: var(--band-black);
  }
  .agent {
    position: absolute; top: 36px; left: 0; right: 0;
    text-align: center;
  }
  .agent__name {
    color: var(--steel-blue);
    font-size: 22px; font-weight: 600; letter-spacing: 1px;
    text-transform: uppercase;
  }
  .agent__license {
    color: var(--text-white);
    font-size: 14px; font-weight: 700; margin-top: 4px;
  }
  .agent__license-label { color: var(--steel-blue); font-weight: 600; }
  .brand-row {
    position: absolute; top: 118px; left: 0; right: 0;
    display: flex; justify-content: center; align-items: center; gap: 16px;
  }
  .brand-row .skyline-art {
    width: 148px; height: 76px;
    background: linear-gradient(180deg, #9a9a9c, var(--skyline-mid));
  }
  .brand-row .divider {
    width: 1px; height: 86px; background: var(--slate-grey);
  }
  .card--front .wordmark__name { font-size: 52px; }
  .card--front .wordmark__sub { font-size: 22px; margin-top: 2px; }
  .contacts {
    position: absolute; top: 236px; left: 0; right: 0;
    display: flex; flex-direction: column; align-items: center; gap: 2px;
    color: var(--text-white); font-size: 16px;
  }
  .contacts__line { display: flex; align-items: center; gap: 6px; }
  .contacts__icon { width: 13px; height: 13px; fill: var(--steel-blue); }
</style>
</head>
<body>
  <section class="card card--back" aria-label="Card back">
    <div class="skyline-decor" role="img" aria-label="Faint illustration of downtown office towers"></div>
    <div class="wordmark">
      <span class="wordmark__name">Velt</span>
      <span class="wordmark__sub">Commercial</span>
    </div>
    <div class="card__stripe-grey"></div>
    <div class="card__stripe-blue"></div>
    <div class="card__stripe-base"></div>
  </section>

  <section class="card card--front" aria-label="Card front">
    <div class="contact-band"></div>
    <div class="agent">
      <p class="agent__name">Derek Holloway</p>
      <p class="agent__license"><span class="agent__license-label">Lic#</span> 07258143</p>
    </div>
    <div class="brand-row">
      <div class="skyline-art" role="img" aria-label="Illustration of a city skyline of office towers"></div>
      <div class="divider"></div>
      <div class="wordmark">
        <span class="wordmark__name">Velt</span>
        <span class="wordmark__sub">Commercial</span>
      </div>
    </div>
    <div class="contacts">
      <p class="contacts__line">
        <svg class="contacts__icon" viewBox="0 0 16 16" aria-hidden="true"><path d="M3.6 1.2l2.3 2.6-1.3 1.9c.9 2 2.6 3.7 4.6 4.6l1.9-1.3 2.6 2.3-1.2 2.4C7.2 14.9 1.1 8.8 1.2 3.2z"/></svg>
        415.555.0172
      </p>
      <p class="contacts__line">
        <svg class="contacts__icon" viewBox="0 0 16 16" aria-hidden="true"><path d="M1 3h14v10H1z M1.8 3.8L8 9l6.2-5.2" stroke="#121212" stroke-width="1"/></svg>
        derek@velt-commercial.example
      </p>
      <p class="contacts__line">
        <svg class="contacts__icon" viewBox="0 0 16 16" aria-hidden="true"><path d="M6.5 9.5l3-3M7 4.5l1.6-1.6a2.6 2.6 0 013.6 3.6L10.6 8M9 11.5l-1.6 1.6a2.6 2.6 0 01-3.6-3.6L5.4 8" fill="none" stroke="#8a9bbb" stroke-width="1.6" stroke-linecap="round"/></svg>
        velt-commercial.example
      </p>
    </div>
    <div class="card__stripe-grey"></div>
    <div class="card__stripe-blue"></div>
    <div class="card__stripe-base"></div>
  </section>
</body>
</html>
```